Korvath Supply Website Redesign

Currently korvathsupply.example is focussed on fulfillment and transport from various products in the BBQ segment. However, no we want to update our business activities to Product Development, Brand Development, Online Positioning, Logistics & Aftersales, and Promotional BBQs. We will be a business for Outdoor Leisure Development from A to Z.

Therefore, we need a brand new website. The colours of the current website may be the same. However, i'd like to keep it clean. More white and use blue and green as accent colours. It is a business to business organization so the website should be looking formal and corporate. However we sell fun products so not too formal and corporate.

Pages we need; Home, About, Contact, Our Services (+ page per service) a place to share our news/blogs.

I have added some sort of mock up of an idea. However it needs some finetuning.

Target Market(s)

Businesses

Industry/Entity Type

Corporate/Logistics/Marketing

Coding

Coded - Design and coding required

Colors

Designer to choose colors to be used in the design.

Requirements
Must have
• Show clear distinguishing of the different services we provide (Product Development, Brand Development, Online Positioning, Logistics & Aftersales and Promotional BBQs). Every service should have its own page too. Besides, I would like to have a blog page to share relevant content.
Nice to have
• Show that we are the expert in Outdoor LEisure Development from A to Z
Should not have
• Be too informal. It may be semi-formal

```html
<!DOCTYPE html>
<html lang="en">
<head>
<meta charset="utf-8">
<title>Korvath Supply – Outdoor Leisure Development</title>
<link href="https://fonts.googleapis.com/css2?family=Open+Sans:wght@400;600;700;800&family=Roboto:wght@400&display=swap" rel="stylesheet">
<style>
:root{
  --green:#3aa13b;
  --green-bright:#3db53f;
  --teal:#2b5468;
  --navy:#243b4a;
  --ink:#161616;
  --text:#3a3a3a;
  --white:#ffffff;
  --footer:#0c0c0e;
  --sky-top:#5f8fc6;
  --sea:#1f4f86;
}
*{margin:0;padding:0;box-sizing:border-box}
html,body{width:1200px;height:3024px;overflow:hidden;background:var(--white)}
body{position:relative;font-family:"Open Sans",Arial,sans-serif;color:var(--text)}
.abs{position:absolute}

/* header */
.site-header{position:absolute;left:0;top:0;width:1200px;height:117px;border-top:4px solid var(--teal);background:var(--white)}
.brand{position:absolute;left:112px;top:34px;display:flex;align-items:center;gap:10px;font-weight:800;font-size:30px;color:var(--teal);letter-spacing:.5px}
.brand-dot{width:30px;height:30px;border-radius:50%;background:var(--teal)}
.main-nav{position:absolute;top:51px;left:0;font-size:14px;font-weight:700;color:var(--ink);text-transform:uppercase}
.main-nav a{position:absolute;white-space:nowrap;text-decoration:none;color:inherit}
.main-nav .current{color:var(--green)}
.nav-hl{position:absolute;left:483px;top:34px;width:38px;height:52px;border-radius:19px;background:#e6ece9}
.quote-btn{position:absolute;left:927px;top:37px;width:160px;height:48px;border:2px solid var(--green);border-radius:24px;color:var(--green);font-weight:700;font-size:14px;display:flex;align-items:center;justify-content:center;text-transform:uppercase}

/* hero */
.hero{position:absolute;left:0;top:117px;width:1200px;height:681px;background:linear-gradient(180deg,var(--sky-top) 0%,#9cbfe0 35%,#4b78a6 55%,var(--sea) 75%,#2a4e78 100%)}
.hero-title{position:absolute;left:0;top:170px;width:1200px;text-align:center;color:var(--white);font-weight:800;font-size:51px;line-height:60px;text-transform:uppercase}
.slide-arrow{position:absolute;top:317px;width:48px;height:48px;border-radius:50%;background:var(--navy);display:flex;align-items:center;justify-content:center}

/* services */
.service-ring{position:absolute;width:240px;height:240px;border-radius:50%;background:var(--white)}
.service-circle{position:absolute;width:212px;height:212px;border-radius:50%;background:linear-gradient(180deg,var(--green-bright) 0%,#33914a 55%,var(--teal) 100%);display:flex;align-items:center;justify-content:center}
.service-label{position:absolute;width:240px;text-align:center;font-weight:700;font-size:19px;line-height:30px;color:var(--ink);text-transform:uppercase}
.service-label.active{color:var(--green)}
.service-text{position:absolute;left:380px;top:977px;width:200px;text-align:center;font-size:14px;line-height:21px;color:#555}
.btn-outline{position:absolute;border:2px solid var(--green);border-radius:26px;color:var(--green);font-weight:700;font-size:14px;display:flex;align-items:center;justify-content:center;text-transform:uppercase;background:transparent}

/* difference */
.team-photo{position:absolute;left:0;top:1208px;width:1200px;height:498px;background:linear-gradient(135deg,#cfd3d6 0%,#8d8f93 40%,#b9bbbd 70%,#e1e3e4 100%)}
.diff-panel{position:absolute;left:112px;top:1428px;width:976px;height:278px;background:rgba(255,255,255,.88)}
.diff-deco{position:absolute;left:364px;top:1397px;width:470px;height:403px;border-radius:0 0 235px 235px;background:#e9f1ec;opacity:.8}
.diff-title{position:absolute;left:0;top:1497px;width:1200px;text-align:center;font-weight:800;font-size:38px;color:var(--ink);text-transform:uppercase}
.body-copy{position:absolute;left:205px;width:790px;text-align:center;font-size:15px;line-height:21.5px;color:var(--text)}

/* news */
.news-title{position:absolute;left:0;top:1912px;width:1200px;text-align:center;font-weight:800;font-size:38px;color:var(--ink);text-transform:uppercase}
.news-card{position:absolute;top:1991px;width:313px;height:361px;border-radius:10px;overflow:hidden}
.news-card .photo{position:absolute;inset:0}
.news-card .caption{position:absolute;left:0;bottom:30px;width:100%;text-align:center;color:var(--white);font-weight:700;font-size:21px;line-height:30px}
.news-overlay{position:absolute;left:14px;top:14px;width:285px;height:333px;border-radius:8px;background:rgba(61,181,63,.88);color:var(--white);text-align:center}
.news-overlay h3{margin-top:34px;font-weight:700;font-size:21px;line-height:30px}
.news-overlay p{margin:8px auto 0;width:250px;font-size:14px;line-height:21.5px}
.btn-white{position:absolute;left:64px;top:241px;width:158px;height:48px;border:2px solid var(--white);border-radius:24px;display:flex;align-items:center;justify-content:center;font-weight:700;font-size:14px;text-transform:uppercase}

/* footer */
.site-footer{position:absolute;left:0;top:2650px;width:1200px;height:374px;background:var(--footer);color:var(--white)}
.footer-brand{position:absolute;left:112px;top:96px;display:flex;align-items:center;gap:10px;font-weight:800;font-size:30px;color:var(--white)}
.footer-brand .brand-dot{background:var(--white)}
.footer-list{position:absolute;top:86px;list-style:none;font-size:17px;line-height:26px}
.footer-list li{position:relative;padding-left:26px}
.footer-list li::before{content:"";position:absolute;left:0;top:9px;width:10px;height:10px;border-radius:50%;background:var(--green-bright)}
.footer-address{position:absolute;left:900px;top:86px;padding-left:27px;font-size:17px;line-height:26px}
.footer-address svg{position:absolute;left:0;top:6px}
.copyright{position:absolute;left:0;top:301px;width:1200px;text-align:center;font-family:"Roboto",Arial,sans-serif;font-size:15px}
</style>
</head>
<body>

<header class="site-header">
  <div class="brand"><span class="brand-dot"></span>Korvath Supply</div>
  <div class="nav-hl"></div>
  <nav class="main-nav">
    <a class="current" style="left:481px">Home</a>
    <a style="left:560px">About</a>
    <a style="left:645px">Our Services</a>
    <a style="left:781px">Contact Us</a>
  </nav>
  <div class="quote-btn">Get a quote</div>
</header>

<section class="hero" role="img" aria-label="Container ship being loaded at a harbour terminal under a blue sky">
  <h1 class="hero-title">Outdoor Leisure<br>Development from A to Z.</h1>
  <div class="slide-arrow" style="left:31px"><svg width="14" height="14" viewBox="0 0 14 14"><path d="M9 2 4 7l5 5" fill="none" stroke="#fff" stroke-width="2"/></svg></div>
  <div class="slide-arrow" style="left:1121px"><svg width="14" height="14" viewBox="0 0 14 14"><path d="M5 2l5 5-5 5" fill="none" stroke="#fff" stroke-width="2"/></svg></div>
</section>

<section class="services">
  <div class="service-ring" style="left:122px;top:672px"></div>
  <div class="service-ring" style="left:360px;top:672px"></div>
  <div class="service-ring" style="left:599px;top:672px"></div>
  <div class="service-ring" style="left:837px;top:672px"></div>

  <div class="service-circle" style="left:136px;top:688px">
    <svg width="110" height="110" viewBox="0 0 110 110" fill="none" stroke="#fff" stroke-width="4"><rect x="30" y="28" width="44" height="38"/><path d="M44 28v14h16V28"/><rect x="8" y="70" width="14" height="30"/><path d="M22 74h30l40-6M22 96h50"/><circle cx="88" cy="22" r="10"/></svg>
  </div>
  <div class="service-circle" style="left:374px;top:688px">
    <svg width="110" height="110" viewBox="0 0 110 110" fill="none" stroke="#fff" stroke-width="4"><rect x="12" y="10" width="50" height="34" rx="4"/><path d="M22 44l-6 10 14-10"/><rect x="52" y="24" width="46" height="30" rx="4"/><path d="M22 22h30M22 32h22"/><circle cx="28" cy="70" r="8"/><circle cx="56" cy="66" r="8"/><circle cx="84" cy="70" r="8"/><path d="M10 100V90a10 10 0 0 1 36 0v10M40 100V86a14 14 0 0 1 32 0v14M66 100V90a10 10 0 0 1 34 0v10"/></svg>
  </div>
  <div class="service-circle" style="left:613px;top:688px">
    <svg width="110" height="110" viewBox="0 0 110 110" fill="none" stroke="#fff" stroke-width="4"><circle cx="55" cy="72" r="30"/><path d="M55 50c-8-10-12-16-12-22a12 12 0 0 1 24 0c0 6-4 12-12 22z"/><circle cx="55" cy="28" r="4"/><path d="M28 22a30 30 0 0 0 0 20M82 22a30 30 0 0 1 0 20"/></svg>
  </div>
  <div class="service-circle" style="left:851px;top:688px">
    <svg width="110" height="110" viewBox="0 0 110 110" fill="none" stroke="#fff" stroke-width="4"><path d="M18 14l14 14-4 4-14-14zM30 30l52 52 10 10-6 6-10-10-52-52"/><path d="M84 14a16 16 0 0 0-18 20L22 78a10 10 0 1 0 10 10l44-44a16 16 0 0 0 20-18l-10 8-10-2-2-10z"/></svg>
  </div>

  <div class="service-label" style="left:122px;top:910px">Product<br>Development</div>
  <div class="service-label active" style="left:360px;top:910px">Brand<br>Development</div>
  <div class="service-label" style="left:599px;top:910px">Online<br>Positioning</div>
  <div class="service-label" style="left:837px;top:910px">Logistics &amp;<br>Aftersales</div>

  <p class="service-text">Lorem ipsum dolor sit amet, consectetur adipiscing elit, sed do eiusmod</p>
  <div class="btn-outline" style="left:401px;top:1059px;width:160px;height:48px">Read more</div>
</section>

<section class="difference">
  <div class="team-photo" role="img" aria-label="Team of colleagues working together around a desk with a tablet"></div>
  <div class="diff-deco"></div>
  <div class="diff-panel"></div>
  <h2 class="diff-title">We make the difference</h2>
  <p class="body-copy" style="top:1566px">Lorem ipsum dolor sit amet, consectetur adipiscing elit, sed do eiusmod tempor incididunt ut labore et dolore magna aliqua. Ut enim ad minim veniam, quis nostrud exercitation ullamco laboris nisi ut aliquip ex ea commodo consequat. Duis aute irure dolor in reprehenderit in voluptate velit esse cillum dolore eu fugiat nulla pariatur. Excepteur sint occaecat cupidatat non proident, sunt in culpa qui officia deserunt mollit anim id est laborum.Lorem ipsum dolor sit amet, consectetur adipiscing elit, sed do eiusmod tempor incididunt ut labore et dolore magna aliqua. Ut enim ad minim veniam, quis nostrud exercitation ullamco laboris nisi ut aliquip ex ea commodo consequat. Duis aute irure dolor in reprehenderit in voluptate velit esse cillum dolore eu fugiat nulla pariatur. Excepteur sint occaecat cupidatat non proident, sunt in culpa qui</p>
  <div class="btn-outline" style="left:520px;top:1774px;width:160px;height:48px">Read more</div>
</section>

<section class="news">
  <h2 class="news-title">Latest news</h2>
  <article class="news-card" style="left:112px">
    <div class="photo" role="img" aria-label="Hands at a laptop with floating document icons" style="background:linear-gradient(160deg,#8a7a62 0%,#4b4a46 50%,#1f2224 100%)"></div>
    <div class="caption">Lorem ipsum dolor<br>sit amet, consectetur</div>
  </article>
  <article class="news-card" style="left:444px">
    <div class="photo" role="img" aria-label="Warehouse interior with stacked goods" style="background:linear-gradient(180deg,#d9dcd8 0%,#8f9a8c 60%,#5c6658 100%)"></div>
    <div class="news-overlay">
      <h3>Lorem ipsum dolor<br>sit amet, consectetur</h3>
      <p>Lorem ipsum dolor sit amet, consectetur adipiscing elit, sed do eiusmod tempor incididunt ut labore et dolore magna incididunt ut labore et dolore magna aliqua.</p>
      <div class="btn-white">Read more</div>
    </div>
  </article>
  <article class="news-card" style="left:775px">
    <div class="photo" role="img" aria-label="Hands drawing on a tablet beside a laptop" style="background:linear-gradient(150deg,#3b3a3c 0%,#6d6a68 50%,#2a2a2d 100%)"></div>
    <div class="caption">Lorem ipsum dolor<br>sit amet, consectetur</div>
  </article>
  <p class="body-copy" style="top:2451px">Lorem ipsum dolor sit amet, consectetur adipiscing elit, sed do eiusmod tempor incididunt ut labore et dolore magna aliqua. Ut enim ad minim veniam, quis nostrud exercitation ullamco laboris nisi ut aliquip ex ea commodo consequat. Duis aute irure dolor in reprehenderit in voluptate velit esse cillum dolore eu fugiat nulla pariatur. Excepteur sint occaecat cupidatat non proident, sunt in culpa qui officia deserunt mollit anim id est laborum.Lorem ipsum dolor sit amet, consectetur adipiscing elit, sed do eiusmod tempor incididunt</p>
</section>

<footer class="site-footer">
  <div class="footer-brand"><span class="brand-dot"></span>Korvath Supply</div>
  <ul class="footer-list" style="left:413px">
    <li>Sitemap</li><li>Home</li><li>About</li><li>Our services</li><li>Contact us</li><li>Blog</li>
  </ul>
  <ul class="footer-list" style="left:612px">
    <li>Product Development</li><li>Brand Development</li><li>Online Positioning</li><li>Logistics &amp; Aftersales</li>
  </ul>
  <address class="footer-address" style="font-style:normal">
    <svg width="10" height="14" viewBox="0 0 10 14"><path d="M5 14C2 9 0 7 0 5a5 5 0 0 1 10 0c0 2-2 4-5 9z" fill="#3db53f"/><circle cx="5" cy="5" r="2" fill="#0c0c0e"/></svg>
    Lindenweg 12<br>5021 KL, Tilburg The<br>Netherlands
  </address>
  <p class="copyright">2021 Copyright - Company name| All Rights Reserved</p>
</footer>

</body>
</html>
```